Webdesign für Kleingruppenreisen in die Südsteiermark
Zielgruppe
Wir sind ein Start-Up Unternehmen, das als Kleingruppenreisen in die Südsteiermark veranstaltet; der Schwerpunkt liegt auf dem Kulinarischen. Zielgruppe sind Geschäftsleute, die diese Kurzreisen (Do-So) für Marketingzwecke oder als Mitarbeiterbonus (oder auch privat) nutzen möchten.
Aufgabenstellung
Die Homepage soll eine Online-Shop Möglichkeit bieten, in der die Reise (bisher gibt es nur einen Ablauf) gebucht werden kann. Optisch sollte sie sich an das bereits von Ihnen erstellte Logo anlehnen und möglichst ansprechende Fotos von der Südsteiermark, Graz, Leoben usw. enthalten. (Siehe die beiden Flyer und das Logo)
Wir haben inzwischen Bildfreigaben von Haldauer und dem Tourismusverband Kellwinden erhalten und können auch eigene Bilder zur Verfügung stellen. Bitte kontaktieren Sie uns dafür, wenn nötig.

```html
<!DOCTYPE html>
<html lang="en">
<head>
<meta charset="utf-8">
<title>Genussweg Reisen – Explore Dream Destination</title>
<link href="https://fonts.googleapis.com/css2?family=Lato:wght@300;400;700;900&family=Kaushan+Script&display=swap" rel="stylesheet">
<style>
:root{
  --orange:#f05a24;
  --yellow:#fde02a;
  --gold:#f8c21a;
  --green:#5cc13a;
  --brand-red:#b3261e;
  --ink:#222;
  --line:#e2e2e2;
  --black:#000;
  --white:#fff;
}
*{box-sizing:border-box;margin:0;padding:0}
html,body{width:1200px;height:3307px;overflow:hidden}
body{position:relative;font-family:'Lato',sans-serif;color:var(--ink);background:var(--white)}
.abs{position:absolute}

/* brand name block (used in header, section and footer) */
.brand-name{display:flex;align-items:center;justify-content:center;gap:10px;background:var(--white);color:var(--brand-red);font-weight:700;text-align:left}
.brand-name .mark{flex:none;border-radius:50%;background:var(--brand-red)}
.brand-name .words{line-height:1.05}

/* header */
.site-header{left:0;top:0;width:1200px;height:90px;background:var(--white)}
.brand{left:88px;top:20px;width:184px;height:102px;z-index:3;font-size:25px}
.brand .mark{width:16px;height:16px}
.main-nav{right:78px;top:27px;display:flex;gap:6px}
.main-nav a{font-size:15px;color:var(--ink);text-decoration:none;padding:12px 14px;border-radius:3px}
.main-nav a.active{background:var(--yellow)}

/* hero */
.hero{left:0;top:90px;width:1200px;height:475px;background:linear-gradient(180deg,#d6582c,#c8502a 45%,#b4532e 75%,#c27a4e)}
.hero-text{left:0;top:140px;width:1200px;text-align:center;color:var(--white)}
.hero-script{font-family:'Kaushan Script',cursive;font-size:88px;line-height:1}
.hero-line{font-weight:300;font-size:74px;letter-spacing:2px;line-height:100px}
.hero-tag{margin-top:8px;font-size:25px;font-weight:700;color:#2b1a08}
.dots{left:590px;top:524px;display:flex;gap:6px}
.dots span{width:15px;height:15px;border-radius:50%;background:var(--white)}
.dots span:first-child{background:var(--yellow)}

/* why */
.why-mark{left:566px;top:586px;width:148px;height:76px;font-size:19px}
.why-mark .mark{width:12px;height:12px}
.section-title{width:1200px;left:0;text-align:center;font-size:35px;font-weight:400}
.section-title b{color:var(--gold);font-weight:700}
.why-text{left:180px;top:745px;width:840px;text-align:center;font-size:20px;font-weight:300;line-height:35px;color:#333}
.slide{top:870px;width:221px;height:207px;box-shadow:0 10px 12px rgba(0,0,0,.3)}
.arrow{top:949px;width:48px;height:48px;border-radius:50%;background:var(--orange);display:flex;align-items:center;justify-content:center}

/* inspired */
.inspired{left:0;top:1118px;width:1200px;height:430px;background:linear-gradient(180deg,#ec7a3e,#d86a30 40%,#b3501e);clip-path:polygon(0 6%,25% 3%,50% 1%,75% 3%,100% 0,100% 92%,70% 96%,50% 95%,25% 97%,0 98%)}
.inspired-title{left:0;top:1150px;width:1200px;text-align:center;font-family:'Kaushan Script',cursive;font-size:58px;color:var(--white)}
.video{left:306px;top:1242px;width:584px;height:290px;background:linear-gradient(160deg,#cfc7a8,#b9b597 55%,#c9b9a0)}
.play{left:512px;top:1306px}
.video-bar{left:306px;top:1532px;width:584px;height:36px;background:#1c1c1c;display:flex;align-items:center;padding:0 12px;gap:10px;color:var(--white);font-size:11px}
.video-bar .track{flex:1;height:8px;background:#000;border-radius:4px}
.video-bar .knob{width:10px;height:10px;border-radius:50%;background:var(--white)}
.video-bar em{font-style:normal;color:#e03a2a}

/* features */
.feature{top:1608px;width:210px}
.feature-head{display:flex;gap:16px;align-items:center}
.feature-icon{width:50px;height:50px;background:var(--green);border-radius:3px;display:flex;align-items:center;justify-content:center}
.feature-head span{font-size:15px;color:#555;line-height:20px}
.feature p{margin-top:22px;font-size:12px;line-height:27px;color:#555;text-align:justify}

/* packages */
.pack-rule{left:548px;top:1920px;width:104px;height:4px;background:var(--ink)}
.card{top:1971px;width:262px;height:360px;border:1px solid var(--line);text-align:center}
.card-head{height:55px;background:var(--orange);color:var(--white);font-size:12.5px;font-weight:900;line-height:20px;padding-top:7px;text-transform:uppercase}
.card-photo{height:137px}
.card h3{margin-top:14px;height:36px;font-size:15px;font-weight:400;color:var(--orange);line-height:18px;padding:0 30px}
.card p{margin-top:8px;font-size:12px;line-height:18px;color:#444;padding:0 14px}
.card-meta{margin-top:12px;border-top:1px solid var(--line);padding-top:10px;font-size:8.5px;color:#888}
.btn-book{display:inline-block;margin-top:8px;background:var(--green);color:var(--white);font-size:12px;padding:4px 19px}

/* orange info */
.info{left:0;top:2372px;width:1200px;height:550px;background:var(--orange)}
.tabs{left:87px;top:2427px;width:493px;height:67px;background:#eee;display:flex;font-size:20px;color:#222}
.tabs div{display:flex;align-items:center;padding:0 22px}
.tabs .on{background:var(--white);width:175px;justify-content:center;border-bottom:4px solid var(--green)}
.info-text{left:87px;top:2525px;width:493px;font-size:17px;line-height:31.5px;color:#ffe89a;font-weight:300;text-align:justify}
.devices{left:605px;top:2392px;width:595px;height:510px;background:radial-gradient(ellipse at 55% 50%,#f48a54 0%,#e8602c 70%,var(--orange) 100%)}

/* footer */
.site-footer{left:0;top:2922px;width:1200px;height:336px;background:var(--black);border-top:4px solid var(--gold)}
.foot-h{top:2944px;font-size:20px;font-weight:700;color:var(--green)}
.foot-menu{top:2996px;font-size:13px;color:var(--white);line-height:35.5px;list-style:none}
.foot-menu .strong{font-size:15px}
.foot-logo{left:252px;top:3145px;width:145px;height:78px;font-size:19px}
.foot-logo .mark{width:12px;height:12px}
.contact-row{left:440px;display:flex;gap:20px;font-size:12px;color:var(--white);line-height:26px;align-items:flex-start}
.contact-row svg{flex:none;margin-top:2px}
.field{left:834px;width:278px;background:var(--white);border:1px solid #ccc;font-size:15px;color:#666;padding:8px 18px;font-weight:300}
.submit{left:834px;top:3180px;width:141px;height:42px;background:var(--yellow);font-size:19px;display:flex;align-items:center;justify-content:center;color:#222}
.copyright{left:0;top:3258px;width:1200px;height:49px;background:#111;color:#ddd;font-size:12px;display:flex;align-items:center;justify-content:center}
</style>
</head>
<body>

<header class="site-header abs"></header>
<div class="brand brand-name abs"><span class="mark"></span><span class="words">Genussweg<br>Reisen</span></div>
<nav class="main-nav abs">
  <a class="active" href="#">HOME</a><a href="#">SERVICES</a><a href="#">ONLINE SHOP</a><a href="#">BLOG</a><a href="#">LEGAL</a><a href="#">CONTACT</a>
</nav>

<section class="hero abs" role="img" aria-label="Photo of a festive old-town street with red banners and crowds, warm orange tint"></section>
<div class="hero-text abs">
  <div class="hero-script">Explore</div>
  <div class="hero-line">DREAM</div>
  <div class="hero-line">DESTINATION</div>
  <div class="hero-tag">YOUR DREAM COMES TRUE HERE</div>
</div>
<div class="dots abs"><span></span><span></span><span></span><span></span></div>

<div class="why-mark brand-name abs"><span class="mark"></span><span class="words">Genussweg<br>Reisen</span></div>
<h2 class="section-title abs" style="top:683px">Why Choosing <b>US?</b></h2>
<p class="why-text abs">Lorem Ipsum is simply dummy text of the printing and typesetting industry. Lorem Ipsum has been the industry's standard dummy text ever since the 1500s</p>

<div class="slide abs" style="left:133px;background:linear-gradient(180deg,#3b8fc8,#6f9e5a 55%,#d9d4c6)" role="img" aria-label="Lakeside alpine village with mountains"></div>
<div class="slide abs" style="left:370px;background:linear-gradient(180deg,#1f6fc4,#7fb0de 55%,#c9c3b4)" role="img" aria-label="Baroque column monument on a city square"></div>
<div class="slide abs" style="left:607px;background:linear-gradient(180deg,#a9c57a,#5f9a2e 50%,#3f7a1e)" role="img" aria-label="Rolling vineyard hills"></div>
<div class="slide abs" style="left:843px;background:linear-gradient(180deg,#4e8a3c,#c23a2e 55%,#8c7a6a)" role="img" aria-label="Red funicular railway cars"></div>
<div class="arrow abs" style="left:113px"><svg width="16" height="16" viewBox="0 0 16 16"><path d="M10 2 4 8l6 6" stroke="#fff" stroke-width="3" fill="none"/></svg></div>
<div class="arrow abs" style="left:1035px"><svg width="16" height="16" viewBox="0 0 16 16"><path d="M6 2l6 6-6 6" stroke="#fff" stroke-width="3" fill="none"/></svg></div>

<section class="inspired abs" role="img" aria-label="Vineyard hills at sunset with orange tint"></section>
<div class="inspired-title abs">Get Inspired</div>
<div class="video abs" role="img" aria-label="Video still of two cyclists on a country path"></div>
<svg class="play abs" width="160" height="160" viewBox="0 0 160 160"><circle cx="80" cy="80" r="72" fill="#fff" stroke="#000" stroke-width="14"/><path d="M60 45v70l58-35z" fill="#000"/></svg>
<div class="video-bar abs">
  <svg width="22" height="22"><circle cx="11" cy="11" r="10" fill="#555"/><path d="M8 6v10l8-5z" fill="#ccc"/></svg>
  <span class="knob"></span><div class="track"></div>
  <span>00:00 / <em>00:00</em></span>
  <svg width="14" height="14"><path d="M1 5h4l5-4v12l-5-4H1z" fill="#aaa"/></svg>
  <div class="track" style="flex:0 0 50px"></div><span class="knob"></span>
  <svg width="36" height="14"><rect x="1" y="1" width="14" height="12" fill="none" stroke="#aaa"/><rect x="20" y="1" width="14" height="12" fill="#777"/></svg>
</div>

<div class="feature abs" style="left:88px">
  <div class="feature-head"><div class="feature-icon"><svg width="28" height="30" viewBox="0 0 28 30"><path d="M3 12a11 11 0 0 1 22 0zM3 12l9 10h4l9-10M12 22h4v6h-4z" fill="none" stroke="#fff" stroke-width="1.6"/></svg></div><span>Special<br>Activities</span></div>
  <p>Lorem Ipsum is simply dummy text of the printing and typesetting industry. Lorem Ipsum has been the industry's standard dummy text ever since the 1500s</p>
</div>
<div class="feature abs" style="left:355px">
  <div class="feature-head"><div class="feature-icon"><svg width="32" height="24" viewBox="0 0 32 24"><path d="M2 14l8-2 14-9 4 2-10 10 10 4-2 2-12-2-10-3z" fill="none" stroke="#fff" stroke-width="1.6"/></svg></div><span>Travel<br>Arrangements</span></div>
  <p>Lorem Ipsum is simply dummy text of the printing and typesetting industry. Lorem Ipsum has been the industry's standard dummy text ever since the 1500s</p>
</div>
<div class="feature abs" style="left:631px">
  <div class="feature-head"><div class="feature-icon"><svg width="30" height="30" viewBox="0 0 30 30"><circle cx="15" cy="15" r="12" fill="none" stroke="#fff" stroke-width="1.6"/><path d="M19 11l-3 6-5 2 3-6z" fill="none" stroke="#fff" stroke-width="1.6"/></svg></div><span>Private<br>Guide</span></div>
  <p>Lorem Ipsum is simply dummy text of the printing and typesetting industry. Lorem Ipsum has been the industry's standard dummy text ever since the 1500s</p>
</div>
<div class="feature abs" style="left:905px">
  <div class="feature-head"><div class="feature-icon"><svg width="30" height="30" viewBox="0 0 30 30"><path d="M15 3c-4 0-7 3-7 7 0 5 7 12 7 12s7-7 7-12c0-4-3-7-7-7zM3 27l6-8h12l6 8z" fill="none" stroke="#fff" stroke-width="1.6"/></svg></div><span>Location<br>Manager</span></div>
  <p>Lorem Ipsum is simply dummy text of the printing and typesetting industry. Lorem Ipsum has been the industry's standard dummy text ever since the 1500s</p>
</div>

<h2 class="section-title abs" style="top:1868px;font-size:33px">BEST HOLIDAY <b>PACKAGES</b></h2>
<div class="pack-rule abs"></div>

<article class="card abs" style="left:130px">
  <div class="card-head">Summer stay for single couple<br>@ $250.00 for 4 nights</div>
  <div class="card-photo" style="background:linear-gradient(180deg,#9fc7e4,#6aa23a 40%,#c9a56a)" role="img" aria-label="Wine glasses on a table overlooking green hills"></div>
  <h3>Vineyard Weekend - Southern Hill Country</h3>
  <p>Lorem Ipsum is simply dummy text of the printing and typesetting industry.</p>
  <div class="card-meta">No of Days: 5 &nbsp;|&nbsp; People: 4</div>
  <span class="btn-book">Book Now</span>
</article>
<article class="card abs" style="left:469px">
  <div class="card-head">Winter stay for single couple @<br>$250.00 for 2 nights</div>
  <div class="card-photo" style="background:linear-gradient(180deg,#5f7f62,#3f6f7a 50%,#8aa4b6)" role="img" aria-label="Modern shell-shaped island structure on a river"></div>
  <h3>Advent Lights - Old Town Walk</h3>
  <p>Lorem Ipsum is simply dummy text of the printing and typesetting industry.</p>
  <div class="card-meta">No of Days: 5 &nbsp;|&nbsp; People: 4</div>
  <span class="btn-book">Book Now</span>
</article>
<article class="card abs" style="left:802px">
  <div class="card-head">Summer stay for single couple<br>@ $250.00 for 3 nights</div>
  <div class="card-photo" style="background:linear-gradient(180deg,#2b2f3e,#8e3a2e 50%,#3a2a22)" role="img" aria-label="Illuminated historic town hall at night"></div>
  <h3>Taste it! Enjoy it! - Mountain Town</h3>
  <p>Lorem Ipsum is simply dummy text of the printing and typesetting industry.</p>
  <div class="card-meta">No of Days: 5 &nbsp;|&nbsp; People: 4</div>
  <span class="btn-book">Book Now</span>
</article>

<section class="info abs"></section>
<div class="tabs abs"><div class="on">Why Best ?</div><div>Features</div><div>Store the Goods</div></div>
<p class="info-text abs">Lorem Ipsum is simply dummy text of the printing and typesetting industry. Lorem Ipsum has been the industry's standard dummy text ever since the 1500s. Lorem Ipsum is simply dummy text of the printing and typesetting industry. Lorem Ipsum has been the industry's standard dummy text ever since the 1500s. Lorem Ipsum is simply dummy text of the printing and typesetting industry. Lorem Ipsum has been the industry's standard dummy text ever since the 1500s. Lorem Ipsum is simply dummy text of the printing and typesetting industry. Lorem Ipsum has been the industry's standard dummy text ever since the 1500s.</p>
<div class="devices abs" role="img" aria-label="Responsive website shown on desktop, laptop, tablet and phone"></div>

<footer class="site-footer abs"></footer>
<div class="foot-h abs" style="left:112px">MENU</div>
<div class="foot-h abs" style="left:478px">CONTACT &nbsp;US</div>
<div class="foot-h abs" style="left:830px">GET &amp; TOUCH WITH US</div>
<ul class="foot-menu abs" style="left:113px"><li>HOME</li><li>SERVICES</li><li class="strong">ONLINE SHOP</li><li>BLOG</li><li>LEGAL</li><li>CONTACT</li></ul>
<ul class="foot-menu abs" style="left:252px"><li>TERMS &amp; CONDITION</li><li>PRIVACY POLICY</li><li>SITEMAP</li></ul>
<div class="foot-logo brand-name abs"><span class="mark"></span><span class="words">Genussweg<br>Reisen</span></div>

<div class="contact-row abs" style="top:2992px"><svg width="18" height="26" viewBox="0 0 18 26"><path d="M9 1a8 8 0 0 0-8 8c0 6 8 16 8 16s8-10 8-16a8 8 0 0 0-8-8z" fill="#fff"/><circle cx="9" cy="9" r="3" fill="#000"/></svg><span>Lorem Ipsum is simply dummy text of the<br>printing and typesetting industry</span></div>
<div class="contact-row abs" style="top:3061px"><svg width="20" height="16" viewBox="0 0 20 16"><rect x="1" y="2" width="18" height="12" fill="none" stroke="#fff" stroke-width="1.4"/><path d="M1 2l9 7 9-7" fill="none" stroke="#fff" stroke-width="1.4"/></svg><span>info@genussweg-post.de</span></div>
<div class="contact-row abs" style="top:3107px"><svg width="24" height="24" viewBox="0 0 24 24"><path d="M5 2l4 5-2 3c1 3 4 6 7 7l3-2 5 4-3 4C10 22 2 14 1 5z" fill="#fff"/></svg><span>000-555-0142</span></div>

<div class="field abs" style="top:2988px;height:36px">Name</div>
<div class="field abs" style="top:3035px;height:36px">Email id</div>
<div class="field abs" style="top:3082px;height:84px">Comments</div>
<div class="submit abs">SUBMIT</div>

<div class="copyright abs">copyright@ www.genusswegreisen.de</div>
</body>
</html>
```